Resposive web site in 4 languages + image gallery + logo design

We need a web page, which will work on all devices.
I have uploaded web page concept.
Company name: Praxelun
Industry/Entity Type
It Company
Logo Text
quality matters
Coding
Coded - Design and coding required
Number of Pages Required
1 page

```html
<!DOCTYPE html>
<html lang="en">
<head>
<meta charset="utf-8">
<title>Praxelun</title>
<link href="https://fonts.googleapis.com/css2?family=Lora:wght@700&family=Open+Sans:wght@400;600;700&family=Oswald:wght@500&display=swap" rel="stylesheet">
<style>
:root{
  --blue:#0b9ae0;
  --navy:#0b5ea6;
  --heading:#1b6cae;
  --text:#555;
  --dark:#3b3b3b;
  --grey-band:#f5f5f5;
  --contact-bg:#f1f1f1;
  --white:#fff;
  --line:#d8d8d8;
}
*{box-sizing:border-box;margin:0;padding:0}
html,body{width:1200px;height:2586px;overflow:hidden}
body{font-family:"Open Sans",Arial,sans-serif;color:var(--text);background:var(--white);position:relative}
.abs{position:absolute}

/* header */
.site-header{position:absolute;left:0;top:0;width:1200px;height:69px;background:var(--white)}
.brand{position:absolute;left:162px;top:18px;font-family:"Lora",Georgia,serif;font-weight:700;font-size:27px;color:var(--navy)}
.main-nav a{position:absolute;top:28px;font-size:11px;color:#333;text-decoration:none;letter-spacing:.3px}
.lang{position:absolute;top:24px;width:28px;height:20px;border:1px solid #bbb;font-size:8px;color:#555;display:flex;align-items:center;justify-content:center}

/* hero */
.hero{position:absolute;left:0;top:69px;width:1200px;height:479px;background:linear-gradient(120deg,#6d5a48 0%,#a58b6d 35%,#c9b49a 55%,#8a6d52 80%,#5b4637 100%)}
.hero-arrow{position:absolute;top:205px}
.hero-title{position:absolute;left:0;width:1200px;top:364px;text-align:center;font-family:"Oswald",sans-serif;font-weight:500;font-size:34px;color:var(--white);letter-spacing:.3px}
.hero-cta{position:absolute;left:519px;top:419px;width:157px;height:34px;border-radius:17px;background:var(--blue);color:var(--white);font-weight:700;font-size:12px;display:flex;align-items:center;justify-content:center;gap:6px;letter-spacing:.4px}

/* section heads */
.section-title{position:absolute;left:0;width:1200px;text-align:center;font-family:"Lora",Georgia,serif;font-weight:700;font-size:18px;color:var(--blue)}
.section-title span{display:inline-block;padding-bottom:6px;border-bottom:2px solid var(--blue)}

/* services */
.band-grey{position:absolute;left:0;width:1200px;background:var(--grey-band)}
.photo{position:absolute;border:1px solid #ccc;padding:4px;background:var(--white)}
.photo div{width:100%;height:100%}
.service-name{position:absolute;font-family:"Lora",Georgia,serif;font-weight:700;font-size:18px;color:var(--heading)}
.service-text{position:absolute;width:392px;font-size:11px;line-height:18px;text-align:justify;color:var(--text)}
.service-text p+p{margin-top:8px}
.tag{position:absolute;width:121px;height:29px;background:var(--blue);color:var(--white);font-size:10.5px;font-weight:600;display:flex;align-items:center;padding-left:14px;gap:8px}
.tag svg{flex:none}

/* about */
.about{position:absolute;left:0;top:1758px;width:1200px;height:357px;background:var(--navy);color:var(--white)}
.about h2{position:absolute;left:160px;top:40px;font-family:"Lora",Georgia,serif;font-size:18px}
.about-text{position:absolute;left:160px;top:78px;width:400px;font-size:10.5px;line-height:17px}
.about-text p+p{margin-top:14px}
.motto{position:absolute;left:160px;top:280px;width:161px;height:27px;border:1px solid var(--white);font-size:10.5px;display:flex;align-items:center;justify-content:center;gap:6px}
.motto b{font-weight:700}

/* contact */
.contact{position:absolute;left:0;top:2115px;width:1200px;height:395px;background:var(--contact-bg)}
.contact-item{position:absolute;width:200px;text-align:center;font-size:11.5px;color:#222}
.contact-item svg{display:block;margin:0 auto 10px}
.divider-v{position:absolute;top:88px;width:1px;height:50px;background:var(--line)}
.divider-h{position:absolute;left:324px;top:168px;width:564px;height:1px;background:var(--line)}
.quote-lead{position:absolute;left:0;width:1200px;top:197px;text-align:center;font-size:10px;color:#444;letter-spacing:.2px}
.field{position:absolute;background:var(--white);font-size:10.5px;color:#444;display:flex;align-items:center;gap:10px;padding-left:14px}
.field.message{align-items:flex-start;padding-top:11px}

/* footer */
.site-footer{position:absolute;left:0;top:2510px;width:1200px;height:76px;background:var(--dark);color:var(--white);font-size:10.5px}
.follow{position:absolute;left:159px;top:30px}
.social{position:absolute;top:24px;width:26px;height:26px}
.footer-links{position:absolute;right:160px;top:31px;font-size:9.5px}
.footer-links span{margin:0 5px}
</style>
</head>
<body>

<header class="site-header">
  <div class="brand">Praxelun</div>
  <nav class="main-nav">
    <a href="#services" style="left:571px">SERVICES</a>
    <a href="#about" style="left:658px">ABOUT US</a>
    <a href="#contact" style="left:753px">CONTACT US</a>
  </nav>
  <div class="lang" style="left:855px">EST</div>
  <div class="lang" style="left:893px">RUS</div>
  <div class="lang" style="left:933px">FIN</div>
  <div class="lang" style="left:972px">ENG</div>
  <div class="lang" style="left:1011px">SOC</div>
</header>

<section class="hero" role="img" aria-label="Craftsman cutting timber with a circular saw in a workshop">
  <svg class="hero-arrow" style="left:128px" width="24" height="50" viewBox="0 0 24 50"><path d="M20 3 L4 25 L20 47" stroke="#fff" stroke-width="4" fill="none" opacity=".85"/></svg>
  <svg class="hero-arrow" style="left:1036px" width="24" height="50" viewBox="0 0 24 50"><path d="M4 3 L20 25 L4 47" stroke="#fff" stroke-width="4" fill="none" opacity=".85"/></svg>
  <h1 class="hero-title">ARE YOU INTERESTED IN AN ESTIMATE?</h1>
  <div class="hero-cta">GET A QUOTE <svg width="10" height="10" viewBox="0 0 10 10"><path d="M1 1l4 4-4 4M5 1l4 4-4 4" stroke="#fff" stroke-width="1.6" fill="none"/></svg></div>
</section>

<h2 class="section-title" id="services" style="top:578px"><span>OUR SERVICES</span></h2>

<!-- Woodworks -->
<div class="photo" style="left:157px;top:648px;width:446px;height:307px"><div role="img" aria-label="Hands sanding a wooden plank on a workbench" style="background:linear-gradient(135deg,#7b5a42,#b48b66 50%,#5e4636)"></div></div>
<h3 class="service-name" style="left:648px;top:667px">Woodworks</h3>
<div class="service-text" style="left:648px;top:700px">Timber is, in essence, a natural and warm material. Wood is also relatively durable and easy to work with, which has made it a favourite of builders throughout history. Our goal is to offer suitable products and quality furniture with installation and after sales service to all of our clients. In order to achieve this, we're this category gallery ready to help our clients in all stages of construction from design to production and maintenance.</div>
<div class="tag" style="left:648px;top:843px"><svg width="10" height="10"><rect x="0" y="3" width="10" height="5" fill="#fff"/></svg>Furniture</div>
<div class="tag" style="left:784px;top:843px"><svg width="10" height="10"><rect x=".5" y=".5" width="9" height="9" stroke="#fff" fill="none"/><path d="M5 0v10M0 5h10" stroke="#fff"/></svg>Windows</div>
<div class="tag" style="left:919px;top:843px"><svg width="10" height="10"><rect x="1.5" y=".5" width="7" height="9" stroke="#fff" fill="none"/></svg>Doors</div>
<div class="tag" style="left:648px;top:891px"><svg width="10" height="10"><path d="M1 9L9 1" stroke="#fff" stroke-width="2"/></svg>Staircases</div>
<div class="tag" style="left:784px;top:891px"><svg width="10" height="10"><rect x="0" y="3" width="10" height="4" fill="#fff"/></svg>Woodcarving</div>
<div class="tag" style="left:919px;top:891px"><svg width="10" height="10"><circle cx="5" cy="5" r="3.5" fill="#fff"/></svg>Graining</div>

<!-- Stoneworks -->
<div class="band-grey" style="top:988px;height:374px"></div>
<h3 class="service-name" style="left:159px;top:1036px">Stoneworks</h3>
<div class="service-text" style="left:159px;top:1068px;width:393px">
  <p>The natural stone found in the ground has been used in construction for centuries because of its durability. A structure built by a skilled craftsman from natural stone is unique, genuine and durable, and perfect for our bracing climate.</p>
  <p>Our experienced craftsmen are ready to help you in all stages of construction from planning to completion.</p>
</div>
<div class="tag" style="left:159px;top:1228px"><svg width="10" height="10"><rect x="0" y="1" width="10" height="4" fill="#fff"/><rect x="4" y="5" width="2" height="5" fill="#fff"/></svg>Walls</div>
<div class="tag" style="left:295px;top:1228px"><svg width="10" height="10"><path d="M0 3h10M2 3v7M8 3v7" stroke="#fff" stroke-width="1.5"/></svg>Terraces</div>
<div class="tag" style="left:431px;top:1228px"><svg width="10" height="10"><path d="M0 2h10M0 6h10M5 2v8" stroke="#fff" stroke-width="1.5"/></svg>Paths</div>
<div class="tag" style="left:159px;top:1276px"><svg width="10" height="10"><path d="M1 4h8l-1 5H2z" fill="#fff"/></svg>Outdoor kitchens</div>
<div class="tag" style="left:295px;top:1276px"><svg width="10" height="10"><rect x=".5" y=".5" width="9" height="9" stroke="#fff" fill="none"/><rect x="3" y="4" width="4" height="6" fill="#fff"/></svg>Fireplaces</div>
<div class="tag" style="left:431px;top:1276px"><svg width="10" height="10"><path d="M5 0C2 4 2 7 5 10C8 7 8 4 5 0z" fill="#fff"/></svg>Smokeries</div>
<div class="photo" style="left:597px;top:1021px;width:444px;height:307px"><div role="img" aria-label="Hands laying granite paving stones with a hammer" style="background:linear-gradient(135deg,#8a7f77,#6e6c70 50%,#a8a4a0)"></div></div>

<!-- Restoration -->
<div class="photo" style="left:157px;top:1407px;width:446px;height:308px"><div role="img" aria-label="Craftsman restoring old wooden window frames" style="background:linear-gradient(135deg,#5b4a3d,#8b7a6a 45%,#b9a284 75%,#6b5a4a)"></div></div>
<h3 class="service-name" style="left:648px;top:1424px">Restoration</h3>
<div class="service-text" style="left:648px;top:1456px">
  <p>It's good to see that fixing old things has become popular again in recent years and people are trying to find ways to preserve valuable old windows and pieces of furniture before deciding to replace them.</p>
  <p>It is possible to give a new life to almost any wooden door, window, piece of furniture or staircase. The extensive experience of our craftsmen will help you achieve the desired result.</p>
</div>
<div class="tag" style="left:648px;top:1600px"><svg width="10" height="10"><rect x="0" y="3" width="10" height="5" fill="#fff"/></svg>Furniture</div>
<div class="tag" style="left:784px;top:1600px"><svg width="10" height="10"><rect x=".5" y=".5" width="9" height="9" stroke="#fff" fill="none"/><path d="M5 0v10M0 5h10" stroke="#fff"/></svg>Windows</div>
<div class="tag" style="left:919px;top:1600px"><svg width="10" height="10"><rect x="1.5" y=".5" width="7" height="9" stroke="#fff" fill="none"/></svg>Doors</div>
<div class="tag" style="left:648px;top:1648px"><svg width="10" height="10"><path d="M1 9L9 1" stroke="#fff" stroke-width="2"/></svg>Staircases</div>
<div class="tag" style="left:784px;top:1648px"><svg width="10" height="10"><rect x="0" y="6" width="10" height="3" fill="#fff"/></svg>Floors</div>
<div class="tag" style="left:919px;top:1648px"><svg width="10" height="10"><circle cx="5" cy="5" r="3.5" fill="#fff"/></svg>Special Projects</div>

<!-- About -->
<section class="about" id="about">
  <h2>About Us</h2>
  <div class="about-text">
    <p>Praxelun is a company whose business operations include making wooden products, restoration and building structures from natural stone.</p>
    <p>All of our products are made by craftsmen and specialists who have extensive experience and knowledge in their fields.</p>
    <p>The products we offer are always handmade and we take the requests and ideas of the specific client into account. We always strive to achieve the best possible quality.</p>
  </div>
  <div class="motto"><b>Quality matters,</b> Praxelun</div>
  <div class="abs" role="img" aria-label="Smiling carpenter holding wooden boards on a building site" style="left:598px;top:28px;width:442px;height:304px;background:linear-gradient(135deg,#c9b08a,#e2d4bf 50%,#9c8a72)"></div>
</section>

<!-- Contact -->
<section class="contact" id="contact">
  <h2 class="section-title" style="top:30px"><span style="color:var(--heading)">Contact Us</span></h2>
  <div class="contact-item" style="left:298px;top:92px">
    <svg width="14" height="18" viewBox="0 0 14 18"><path d="M7 1C3.7 1 1 3.6 1 6.8 1 11 7 17 7 17s6-6 6-10.2C13 3.6 10.3 1 7 1z" fill="#666"/><circle cx="7" cy="6.8" r="2.2" fill="#f1f1f1"/></svg>
    Kaseliku 12, 10115 Tallinn, Estonia</div>
  <div class="divider-v" style="left:521px"></div>
  <div class="contact-item" style="left:500px;top:92px">
    <svg width="18" height="18" viewBox="0 0 18 18"><path d="M4 1l3 4-2 2c1 2.5 3.5 5 6 6l2-2 4 3-2 3C8 16 2 10 1 3z" fill="#666"/></svg>
    +372 55 01234</div>
  <div class="divider-v" style="left:697px"></div>
  <div class="contact-item" style="left:705px;top:92px">
    <svg width="20" height="16" viewBox="0 0 20 16"><rect x="1" y="1" width="18" height="14" fill="none" stroke="#666" stroke-width="1.6"/><path d="M1 2l9 7 9-7" fill="none" stroke="#666" stroke-width="1.6"/></svg>
    hello@praxelun.ee</div>
  <div class="divider-h"></div>
  <p class="quote-lead">PLEASE FILL IN THE FOLLOWING FIELDS IF YOU WOULD LIKE A PRICE QUOTE</p>
  <div class="field" style="left:331px;top:231px;width:259px;height:37px"><svg width="9" height="10"><circle cx="4.5" cy="3" r="2.5" fill="#444"/><path d="M0 10c0-3 2-4.5 4.5-4.5S9 7 9 10z" fill="#444"/></svg>Name</div>
  <div class="field" style="left:331px;top:275px;width:259px;height:36px"><svg width="9" height="10"><path d="M2 0l2 3-1 1.5c.8 1.4 1.8 2.4 3 3L7.5 6 10 8 8.5 10C4 9 1 5 1 1z" fill="#444"/></svg>Telephone</div>
  <div class="field" style="left:331px;top:323px;width:259px;height:34px"><svg width="10" height="8"><rect x=".5" y=".5" width="9" height="7" fill="none" stroke="#444"/><path d="M.5 1l4.5 3.5L9.5 1" fill="none" stroke="#444"/></svg>E mail</div>
  <div class="field message" style="left:609px;top:231px;width:262px;height:126px"><svg width="9" height="10"><path d="M0 0h6l3 3v7H0z" fill="#444"/></svg>Message</div>
</section>

<footer class="site-footer">
  <span class="follow">Follow us on</span>
  <div class="social" role="img" aria-label="Social network link" style="left:240px;background:#1f74c4"></div>
  <div class="social" role="img" aria-label="Social network link" style="left:274px;background:#1da1e6"></div>
  <div class="social" role="img" aria-label="Social network link" style="left:307px;background:#e0533f"></div>
  <div class="footer-links">Home<span>|</span>About Us<span>|</span>Services<span>|</span>Contact us<span>|</span>Copyrights @ 2016 All Rights Reserved</div>
</footer>

</body>
</html>
```